Rebrand stationary with recently completed logo design

Need new business cards, thank you cards, letterhead, envelopes and presentation folders. The designs will be sent to a separate production firm so I need the files to be print ready.

My contact info
Reko Haliburn

Office 604-318-5047
Fax 604-371-8054

Email reko@glazemark.ca
website www.glazemark.ca

315-14720 62nd Avenue,
Langley, BC, V2K 3R8

Target Market(s)

Homeowners, businesses and contractors

Industry/Entity Type

Business

Font styles to use
Sans Serif

Colors
34a7d7

Requirements
Must have
• Like to have one side of the business card a solid color with the logo in all white. The side with all the text to be a white background
• I find the current blue on the front of the card with the white logo too dark.
Should not have
• Gradient colors

```html
<!DOCTYPE html>
<html lang="en">
<head>
<meta charset="utf-8">
<title>Glazemark Business Card</title>
<link rel="stylesheet" href="https://fonts.googleapis.com/css2?family=Source+Sans+3:wght@400;600&display=swap">
<style>
  :root {
    --backdrop: #2b2b2b;
    --card-white: #f3f3f3;
    --brand-blue: #0b8fd0;
    --accent-blue: #1a96d6;
    --slate: #414c56;
    --text-grey: #55595d;
    --rule-grey: #6d7176;
    --white: #ffffff;
  }
  * { margin: 0; padding: 0; box-sizing: border-box; }
  html, body {
    width: 1200px;
    height: 960px;
    overflow: hidden;
    background: var(--backdrop);
    font-family: "Source Sans 3", "Helvetica Neue", Arial, sans-serif;
  }
  .stage { position: relative; width: 1200px; height: 960px; }

  .card {
    position: absolute;
    width: 600px;
    height: 342px;
  }
  .card-front { left: 302px; top: 129px; background: var(--card-white); }
  .card-back { left: 299px; top: 488px; background: var(--brand-blue); }

  /* Front brand lockup */
  .brand-front {
    position: absolute;
    right: 36px;
    top: 112px;
    display: flex;
    align-items: center;
    gap: 10px;
  }
  .brand-mark { display: block; background: var(--slate); }
  .brand-front .brand-mark { width: 14px; height: 14px; }
  .brand-front .brand-name {
    font-size: 32px;
    font-weight: 400;
    letter-spacing: 0.5px;
    color: var(--slate);
    line-height: 1;
  }

  /* Holder */
  .holder-name {
    position: absolute;
    left: 29px;
    top: 234px;
    font-size: 19px;
    font-weight: 600;
    color: var(--slate);
    letter-spacing: 0.2px;
  }
  .holder-name .given { color: var(--accent-blue); }
  .holder-rule {
    position: absolute;
    left: 29px;
    top: 266px;
    width: 533px;
    height: 1px;
    background: var(--rule-grey);
  }

  .contact-row {
    position: absolute;
    left: 29px;
    top: 278px;
    display: flex;
    font-size: 13.5px;
    color: var(--text-grey);
    line-height: 19px;
  }
  .contact-group { display: flex; flex-direction: column; }
  .contact-address { width: 176px; }
  .contact-divider {
    width: 1px;
    height: 34px;
    margin-top: 2px;
    background: var(--rule-grey);
  }
  .contact-phones { padding-left: 28px; width: 171px; }
  .contact-web { padding-left: 40px; }
  .contact-line { display: flex; align-items: center; gap: 7px; }
  .contact-line svg { width: 15px; height: 13px; flex: none; }

  /* Back brand lockup */
  .brand-back {
    position: absolute;
    left: 0;
    right: 0;
    top: 0;
    bottom: 0;
    display: flex;
    align-items: center;
    justify-content: center;
    gap: 16px;
  }
  .brand-back .brand-mark { width: 26px; height: 26px; background: var(--white); }
  .brand-back .brand-name {
    font-size: 46px;
    font-weight: 400;
    letter-spacing: 1px;
    color: var(--white);
    line-height: 1;
  }
</style>
</head>
<body>
<main class="stage">

  <section class="card card-front" aria-label="Business card, contact side">
    <div class="brand-front">
      <span class="brand-mark" aria-hidden="true"></span>
      <span class="brand-name">GLAZEMARK</span>
    </div>

    <h1 class="holder-name"><span class="given">REKO</span> HALIBURN</h1>
    <div class="holder-rule"></div>

    <div class="contact-row">
      <div class="contact-group contact-address">
        <span>315-14720 62nd Avenue</span>
        <span>Langley, BC, V2K 3R8</span>
      </div>
      <div class="contact-divider"></div>
      <div class="contact-group contact-phones">
        <span class="contact-line">
          <svg viewBox="0 0 15 13" aria-label="Office"><path fill="var(--accent-blue)" d="M3.2 0.5 5.3 3 4.2 4.5c.8 1.7 2.2 3.1 3.9 3.9l1.5-1.1 2.5 2.1-1.3 2.1C6.300 11.300 1.900 6.900 1.500 2.100Z"/></svg>
          604-318-5047
        </span>
        <span class="contact-line">
          <svg viewBox="0 0 15 13" aria-label="Fax"><rect x="4" y="1" width="7" height="4" fill="var(--accent-blue)"/><rect x="1" y="5" width="13" height="5" rx="1" fill="var(--accent-blue)"/><rect x="4" y="9" width="7" height="3" fill="var(--accent-blue)"/></svg>
          604-371-8054
        </span>
      </div>
      <div class="contact-divider"></div>
      <div class="contact-group contact-web">
        <span class="contact-line">
          <svg viewBox="0 0 15 13" aria-label="Email"><rect x="1.5" y="2.5" width="12" height="8" fill="var(--accent-blue)"/><path d="M1.5 2.5 7.5 7 13.5 2.5" fill="none" stroke="var(--card-white)" stroke-width="1"/></svg>
          reko@glazemark.ca
        </span>
        <span class="contact-line">
          <svg viewBox="0 0 15 13" aria-label="Website"><circle cx="7.5" cy="6.5" r="5.5" fill="var(--accent-blue)"/><path d="M2 6.5h11M7.5 1c-2 2.5-2 8.5 0 11M7.5 1c2 2.5 2 8.5 0 11" fill="none" stroke="var(--card-white)" stroke-width="0.8"/></svg>
          www.glazemark.ca
        </span>
      </div>
    </div>
  </section>

  <section class="card card-back" aria-label="Business card, brand side">
    <div class="brand-back">
      <span class="brand-mark" aria-hidden="true"></span>
      <span class="brand-name">GLAZEMARK</span>
    </div>
  </section>

</main>
</body>
</html>
```